Harborline Family Counsel Billboard

We are looking for a billboard design for a Florida divorce law firm. We are unique in the legal field for offering flat fee pricing. Other law firms are expensive, charging hourly rates. We have A LOT of lawyers advertising for personal injury, so we are looking for something fun that will catch the attention and drive home the message that we are an affordable firm to hire for their divorce because we charge a fixed fee. We want people to be directed to steadyratesplit.com

Target Market(s)

Individual seeking a fast and affordable divorce at a fixed fee instead of hourly

Industry/Entity Type

Legal

Requirements
Must have
• Name of firm, logo, steadyratesplit.com, and in small font: Main Office Jacksonville
Should not have
• Promises. Price

```html
<!DOCTYPE html>
<html lang="en">
<head>
<meta charset="utf-8">
<title>Harborline Family Counsel Billboard</title>
<link rel="stylesheet" href="https://fonts.googleapis.com/css2?family=Poppins:wght@500;600;800&family=Questrial&display=swap">
<style>
  :root {
    --navy: #1d3f66;
    --navy-deep: #16355a;
    --gold: #c99a22;
    --gold-dark: #a87c17;
    --ink: #111111;
    --white: #ffffff;
    --stage: #e4e4e4;
  }
  html, body {
    margin: 0;
    padding: 0;
    width: 1081px;
    height: 1200px;
    overflow: hidden;
    background: var(--stage);
  }
  .billboard {
    position: absolute;
    left: 40px;
    top: 454px;
    width: 1001px;
    height: 292px;
    background: var(--white);
    overflow: hidden;
    box-shadow: 0 4px 10px rgba(0,0,0,0.25);
    font-family: "Poppins", sans-serif;
  }
  .headline-band {
    position: absolute;
    left: 0; top: 0;
    width: 100%;
    height: 178px;
    background: linear-gradient(180deg, #22466f 0%, var(--navy-deep) 100%);
  }
  .bottom-shapes {
    position: absolute;
    left: 0; top: 0;
    width: 1001px;
    height: 292px;
  }
  .attorney-photo {
    position: absolute;
    left: 0;
    top: 23px;
    width: 235px;
    height: 269px;
    background: linear-gradient(180deg, #3a3f48 0%, #1c222c 60%, #12161d 100%);
    clip-path: polygon(26% 0, 62% 0, 66% 42%, 88% 52%, 100% 100%, 0 100%, 0 50%, 22% 42%);
  }
  .rings-photo {
    position: absolute;
    left: 814px;
    top: 48px;
    width: 156px;
    height: 100px;
    border-radius: 50%;
    background: radial-gradient(ellipse at 45% 45%, #f3d27a 0%, #d7a93b 45%, rgba(29,63,102,0) 72%);
  }
  .headline {
    position: absolute;
    left: 160px;
    width: 680px;
    margin: 0;
    text-align: center;
    line-height: 1;
    white-space: nowrap;
    text-transform: uppercase;
  }
  .headline.firm {
    top: 28px;
    font-size: 41px;
    font-weight: 600;
    color: var(--gold);
  }
  .headline.offer {
    top: 70px;
    font-size: 52px;
    font-weight: 800;
    color: var(--white);
    letter-spacing: -0.5px;
  }
  .headline.offer-sub {
    top: 119px;
    font-size: 52px;
    font-weight: 800;
    color: var(--gold);
    letter-spacing: -0.5px;
  }
  .web-address {
    position: absolute;
    left: 256px;
    top: 187px;
    font-size: 33px;
    font-weight: 600;
    color: var(--ink);
    line-height: 1;
    white-space: nowrap;
  }
  .office {
    position: absolute;
    left: 264px;
    top: 246px;
    display: flex;
    align-items: center;
    gap: 14px;
    font-family: "Questrial", sans-serif;
    font-size: 29px;
    letter-spacing: 2px;
    color: var(--white);
    line-height: 1;
    white-space: nowrap;
  }
  .firm-mark {
    position: absolute;
    left: 795px;
    top: 192px;
    width: 160px;
    text-align: center;
  }
  .firm-mark .dot {
    display: block;
    width: 46px;
    height: 46px;
    margin: 0 auto 8px;
    border-radius: 50%;
    background: var(--navy);
  }
  .firm-mark .name {
    font-family: "Poppins", sans-serif;
    font-size: 13px;
    font-weight: 500;
    color: var(--navy);
    line-height: 1.2;
    letter-spacing: 1px;
    text-transform: uppercase;
  }
</style>
</head>
<body>
  <section class="billboard">
    <div class="headline-band"></div>

    <svg class="bottom-shapes" viewBox="0 0 1001 292" aria-hidden="true">
      <defs>
        <linearGradient id="goldBand" x1="0" y1="0" x2="1" y2="0">
          <stop offset="0" stop-color="#b98a1d"/>
          <stop offset="0.6" stop-color="#c79c2f"/>
          <stop offset="1" stop-color="#a87c17"/>
        </linearGradient>
      </defs>
      <polygon points="200,235 722,235 768,292 200,292" fill="url(#goldBand)"/>
      <polygon points="738,235 752,235 800,292 786,292" fill="var(--navy)"/>
    </svg>

    <div class="rings-photo" role="img" aria-label="Photo of two gold wedding rings, one cracked"></div>

    <p class="headline firm">Harborline Family Counsel</p>
    <p class="headline offer">We charge a fixed fee</p>
    <p class="headline offer-sub">On your divorce</p>

    <div class="web-address">www.steadyratesplit.com</div>

    <div class="office">
      <svg width="22" height="26" viewBox="0 0 22 26" aria-hidden="true">
        <path d="M11 1C6 1 2.5 4.6 2.5 9.3 2.5 15 11 23 11 23s8.5-8 8.5-13.7C19.5 4.6 16 1 11 1z" fill="none" stroke="#1d3f66" stroke-width="2.6"/>
        <circle cx="11" cy="9.3" r="3" fill="#1d3f66"/>
        <ellipse cx="11" cy="24.5" rx="6" ry="1.4" fill="#1d3f66"/>
      </svg>
      <span>Main Office Jacksonville</span>
    </div>

    <div class="firm-mark">
      <span class="dot"></span>
      <div class="name">Harborline Family<br>Counsel</div>
    </div>

    <div class="attorney-photo" role="img" aria-label="Portrait photo of the attorney in a dark suit and gold tie"></div>
  </section>
</body>
</html>
```